Web design for financial services

A modern web design of financial services (brokerage firm)
Req.s and technology tags :
- Very mobile friendly.
- One paged with some inner pages.
- Animated sticky header .
- Member login area for e-trade.
- Support RTL language.
- HTML & CSS.

The logo will be Home link
• MPTR :
WHO WE ARE
Content :
i) Board of Directors
ii) Mission Statement
iii) Corporate Values
iv) Regulations
• Financial Services :
WHAT WE DO
Content:
i) Electronic trading
ii) Trading desk
iii) Institutional
iv) Investors Education
• News
• Market Tools
• Forms---- opens new page
• Careers---- opens new page
• Contact Us----opens new page

The website is :
http://www.mptr-doha-example.com/

The logo need some changes to be more modern and impressively , but with keeping same structure .

Some related websites :
https://www.lv-bourse.example/

financial market

Financial Service

Coded - Design and coding required

2 page

• same fonts of http://www.kwdholdings.example/

• - Very mobile friendly.
• - One paged with some inner pages.
• - Animated sticky header .
• - Member login area for e-trade.
• - Support RTL language.
• - HTML & CSS.
• Slider , some Qatari theme,
• i like the video inside the home page
• ex :http://www.kwdholdings.example/

```html
<!DOCTYPE html>
<html lang="en">
<head>
<meta charset="utf-8">
<title>About MPTR</title>
<link rel="stylesheet" href="https://fonts.googleapis.com/css2?family=Open+Sans:ital,wght@0,400;0,600;0,700;0,800;1,400;1,600&display=swap">
<style>
:root{
  --brand-red:#9b1c1f;
  --ink:#1b1b1b;
  --body-text:#333;
  --muted:#8a8a8a;
  --soft-grey:#f1f1f1;
  --line:#dcdcdc;
  --footer-bg:#000;
  --white:#fff;
}
*{margin:0;padding:0;box-sizing:border-box}
html,body{width:1200px;height:3066px;overflow:hidden}
body{position:relative;background:var(--white);font-family:"Open Sans",Arial,sans-serif;color:var(--body-text)}
.abs{position:absolute}
.backdrop{position:absolute;left:0;top:0}

/* header */
.site-header{position:absolute;left:0;top:0;width:1200px;height:120px;background:var(--white);z-index:5}
.brand{position:absolute;left:76px;top:46px;display:flex;align-items:center;gap:10px;color:var(--ink);font-weight:800;font-size:36px;letter-spacing:.5px;text-decoration:none}
.brand-mark{width:20px;height:20px;background:var(--brand-red)}
.util-bar{position:absolute;right:78px;top:27px;display:flex;gap:10px}
.etrade-btn{background:var(--brand-red);color:var(--white);font-size:10px;font-weight:700;padding:5px 10px;border-radius:3px;letter-spacing:.3px}
.lang-btn{border:1px solid var(--line);color:var(--ink);font-size:10px;font-weight:600;padding:4px 10px;border-radius:3px}
.main-nav{position:absolute;right:78px;top:82px;display:flex;gap:30px}
.main-nav a{font-size:12.5px;font-weight:700;color:var(--ink);text-decoration:none;letter-spacing:.2px}
.main-nav a.is-active{color:var(--brand-red)}

.hero-title{left:0;width:1200px;top:300px;text-align:center;color:var(--white);font-size:64px;font-weight:700;letter-spacing:1px}

.section-title{font-size:26px;font-weight:800;color:var(--ink);letter-spacing:.5px}
.lead{font-style:italic;color:var(--brand-red);font-size:14px;line-height:24px;width:460px}
.text-col{font-size:10.5px;line-height:19px;width:212px;color:var(--body-text)}

.board-intro{left:505px;top:1220px;width:545px;font-size:14.5px;line-height:25px}
.director-card{position:absolute;top:1318px;width:272px;height:405px;background:var(--white);border:1px solid var(--line);border-radius:136px 136px 6px 6px;text-align:center}
.portrait{display:block;margin:40px auto 0;width:112px;height:112px;border-radius:50%;background:radial-gradient(circle at 50% 45%,#d9b7a0 0,#a88672 55%,#6d5a50 100%);border:3px solid #eee}
.director-name{margin-top:22px;color:var(--brand-red);font-size:14px;font-weight:700}
.director-quote{margin:12px auto 0;width:206px;font-style:italic;font-size:11.5px;line-height:23px;color:var(--body-text)}
.q{color:var(--brand-red);font-weight:800;font-style:normal;font-size:18px;line-height:10px}
.social{display:flex;justify-content:center;gap:8px;margin-top:16px}
.social span{width:22px;height:22px;border:1px solid #9a9a9a;border-radius:50%}

/* footer */
.site-footer{left:0;top:2820px;width:1200px;height:246px;background:var(--footer-bg);color:var(--white);text-align:center}
.footer-brand{margin-top:40px;display:inline-flex;align-items:center;gap:9px;font-size:28px;font-weight:800}
.footer-brand .brand-mark{width:16px;height:16px;background:var(--white)}
.footer-nav{margin-top:24px;font-size:13px;font-weight:700;letter-spacing:.3px}
.footer-nav span{margin:0 12px}
.copyright{margin-top:12px;font-size:10px;color:#9a9a9a}
.footer-social{display:flex;justify-content:center;gap:8px;margin-top:20px}
.footer-social span{width:24px;height:24px;border:1px solid #bbb;border-radius:50%}
</style>
</head>
<body>

<svg class="backdrop" width="1200" height="3066" viewBox="0 0 1200 3066" aria-hidden="true">
  <polygon points="0,1114 375,1043 1200,1200 1200,1890 640,1856 375,1806 0,1872" fill="#f1f1f1"/>
  <polygon points="0,2440 375,2372 640,2432 1200,2500 1200,2500 0,2500" fill="#ececec"/>
</svg>

<svg class="abs" style="left:0;top:120px" width="1200" height="480" viewBox="0 120 1200 480" role="img" aria-label="Night skyline of Doha towers">
  <defs><linearGradient id="heroGrad" x1="0" y1="0" x2="0" y2="1"><stop offset="0" stop-color="#0c0d14"/><stop offset=".6" stop-color="#23253a"/><stop offset="1" stop-color="#3a3142"/></linearGradient></defs>
  <polygon points="0,120 1200,120 1200,600 640,527 0,592" fill="url(#heroGrad)"/>
</svg>

<svg class="abs" style="left:640px;top:560px" width="560" height="625" viewBox="640 560 560 625" role="img" aria-label="Photo of lit towers along the Doha waterfront at dusk">
  <defs><linearGradient id="coGrad" x1="0" y1="0" x2="0" y2="1"><stop offset="0" stop-color="#25346a"/><stop offset=".6" stop-color="#3b4c7e"/><stop offset="1" stop-color="#6d5a4a"/></linearGradient></defs>
  <polygon points="640,562 1200,600 1200,1185 640,1120" fill="url(#coGrad)"/>
</svg>

<svg class="abs" style="left:640px;top:1856px" width="560" height="644" viewBox="640 1856 560 644" role="img" aria-label="Photo of a glowing world map with a rising stock chart">
  <defs><linearGradient id="viGrad" x1="0" y1="0" x2="1" y2="1"><stop offset="0" stop-color="#5fa9b6"/><stop offset=".5" stop-color="#2e6f86"/><stop offset="1" stop-color="#1b3f5a"/></linearGradient></defs>
  <polygon points="640,1856 1200,1905 1200,2483 640,2432" fill="url(#viGrad)"/>
</svg>

<svg class="abs" style="left:0;top:2480px" width="1200" height="340" viewBox="0 0 1200 340" role="img" aria-label="Illustrated Doha skyline in red tones">
  <defs><linearGradient id="skyGrad" x1="0" y1="0" x2="0" y2="1"><stop offset="0" stop-color="#ffffff"/><stop offset=".35" stop-color="#e8cfcd"/><stop offset="1" stop-color="#a9524f"/></linearGradient></defs>
  <rect width="1200" height="340" fill="url(#skyGrad)"/>
</svg>

<header class="site-header">
  <a class="brand" href="#"><span class="brand-mark"></span>MPTR</a>
  <div class="util-bar">
    <span class="etrade-btn">MPTR E-TRADE</span>
    <span class="lang-btn">ENGLISH ▾</span>
  </div>
  <nav class="main-nav">
    <a class="is-active" href="#">MPTR</a>
    <a href="#">FINANCIAL SERVICE</a>
    <a href="#">NEWS</a>
    <a href="#">MARKET TOOL</a>
    <a href="#">FORMS</a>
    <a href="#">CAREERS</a>
    <a href="#">CONTACT US</a>
  </nav>
</header>

<h1 class="abs hero-title">ABOUT MPTR</h1>

<section>
  <h2 class="abs section-title" style="left:160px;top:628px">OUR COMPANY</h2>
  <p class="abs lead" style="left:160px;top:680px">Meridian Prime Trading is a Private Qatari company that aims to provide secure and technologically advanced methods of trading to its clients. Those facilities enables clients to trade faster, more secure &amp; private. Having this strategy in our in minds, with this online portal we begin.</p>
  <p class="abs text-col" style="left:160px;top:818px">Our desk pairs careful research with fast order routing, so each client can act on market moves with confidence. We keep fees clear, reports simple and support close at hand, from the first account setup to every trade that follows after.</p>
  <p class="abs text-col" style="left:407px;top:818px">Our desk pairs careful research with fast order routing, so each client can act on market moves with confidence. We keep fees clear, reports simple and support close at hand, from the first account setup to every trade that follows after.</p>
</section>

<section>
  <h2 class="abs section-title" style="left:160px;top:1240px">BOARD OF DIRECTORS</h2>
  <p class="abs board-intro">We are guided by a board with deep roots in regional markets, bringing long experience in banking, regulation and investment to every decision we make for our clients and partners.</p>

  <article class="director-card" style="left:160px">
    <span class="portrait" role="img" aria-label="Portrait photo of board member"></span>
    <h3 class="director-name">Mr. Karim Al Haddad</h3>
    <p class="director-quote"><span class="q">“</span> Trust is earned one trade at a time, and our duty is to keep every client informed, protected and ready for the next market, with clear advice and steady service. <span class="q">”</span></p>
    <div class="social"><span></span><span></span><span></span></div>
  </article>
  <article class="director-card" style="left:464px">
    <span class="portrait" role="img" aria-label="Portrait photo of board member"></span>
    <h3 class="director-name">Shaikh Nasser Bin</h3>
    <p class="director-quote"><span class="q">“</span> Trust is earned one trade at a time, and our duty is to keep every client informed, protected and ready for the next market, with clear advice and steady service. <span class="q">”</span></p>
    <div class="social"><span></span><span></span><span></span></div>
  </article>
  <article class="director-card" style="left:766px">
    <span class="portrait" role="img" aria-label="Portrait photo of board member"></span>
    <h3 class="director-name">Mr. Yousef Darwish</h3>
    <p class="director-quote"><span class="q">“</span> Trust is earned one trade at a time, and our duty is to keep every client informed, protected and ready for the next market, with clear advice and steady service. <span class="q">”</span></p>
    <div class="social"><span></span><span></span><span></span></div>
  </article>
</section>

<section>
  <h2 class="abs section-title" style="left:160px;top:1932px">OUR VISION</h2>
  <p class="abs lead" style="left:160px;top:1984px">We intent to optimize all company resources to position ourselves as an unique competitive business model with the goal of generating highly competitive returns for our clients and shareholders, by providing accurate, rapid and reliable order execution, attractive financial products</p>
  <p class="abs text-col" style="left:160px;top:2118px">Our desk pairs careful research with fast order routing, so each client can act on market moves with confidence. We keep fees clear, reports simple and support close at hand, from the first account setup to every trade that follows after.</p>
  <p class="abs text-col" style="left:407px;top:2118px">Our desk pairs careful research with fast order routing, so each client can act on market moves with confidence. We keep fees clear, reports simple and support close at hand, from the first account setup to every trade that follows after.</p>
</section>

<footer class="abs site-footer">
  <div class="footer-brand"><span class="brand-mark"></span>MPTR</div>
  <div class="footer-nav">MPTR<span>|</span>FINACIAL SERVICE<span>|</span>NEWS<span>|</span>MARKET TOOL<span>|</span>CAREERS<span>|</span>CONTACT US</div>
  <p class="copyright">©2017. All Rights Reserved | MPTR Qatar | Copyright, Legal and Privacy Statement,Disclaimers and Legal Information</p>
  <div class="footer-social"><span></span><span></span><span></span><span></span><span></span></div>
</footer>

</body>
</html>
```